BRINDLEWOOD EXTRA VIRGIN OLIVE OIL

I needs a design for an Australian Extra Virgin Olive Oil.

The label will go on a round clear bottle

The label size front and back is 145mm high x 60mm wide.

The important points for the design are as follows.

I want to see elegant olives on the label so that non English speaking markets can easily understand its olive oil. I want it too look classy . IT must also look Australian but I don't want to see kangaroos just colours that reflect Australia.

The mandatory info on front label will be

BRINDLEWOOD

Cold Pressed
EXTRA VIRGIN OLIVE OIL

AUSTRALIAN

1 litre

```html
<!DOCTYPE html>
<html lang="en">
<head>
<meta charset="utf-8">
<title>Brindlewood – Extra Virgin Oil Label</title>
<link href="https://fonts.googleapis.com/css2?family=Cinzel:wght@400&family=Exo+2:wght@300;400&display=swap" rel="stylesheet">
<style>
  :root {
    --sheet: #ffffff;
    --ink: #2a2a2a;
    --rule: #8a8a8a;
    --dim: #c4c4c4;
    --cream: #ede9e4;
    --maroon: #402124;
    --maroon-text: #3f2224;
    --cream-text: #ece6e0;
  }
  * { box-sizing: border-box; margin: 0; padding: 0; }
  html, body { width: 1200px; height: 848px; overflow: hidden; background: var(--sheet); }
  .sheet { position: relative; width: 1200px; height: 848px; font-family: "Exo 2", sans-serif; }

  .sheet-header {
    position: absolute; left: 56px; top: 31px; width: 1081px; height: 21px;
    border-top: 1px solid var(--rule); border-bottom: 1px solid var(--rule);
    display: flex; justify-content: space-between; align-items: center;
    font-size: 13px; letter-spacing: 1.2px; color: var(--ink); text-transform: uppercase;
  }
  .sheet-footer-rule { position: absolute; left: 56px; top: 811px; width: 1081px; border-top: 1px solid var(--rule); }

  .dimension-width {
    position: absolute; top: 117px; height: 32px;
    border-left: 1px solid var(--dim); border-right: 1px solid var(--dim);
  }
  .dimension-width::before {
    content: ""; position: absolute; left: 0; right: 0; top: 5px; border-top: 1px solid var(--dim);
  }
  .dimension-width span {
    position: absolute; left: 50%; top: -6px; transform: translateX(-50%);
    background: var(--sheet); padding: 0 3px; font-size: 10px; color: #aaa;
  }
  .dimension-height {
    position: absolute; top: 161px; height: 582px; width: 32px;
    border-top: 1px solid var(--dim); border-bottom: 1px solid var(--dim);
  }
  .dimension-height::before {
    content: ""; position: absolute; top: 0; bottom: 0; left: 0; border-left: 1px solid var(--dim);
  }
  .dimension-height span {
    position: absolute; left: -9px; top: 50%; transform: translateY(-50%) rotate(-90deg);
    background: var(--sheet); padding: 0 3px; font-size: 10px; color: #aaa;
  }

  .label {
    position: absolute; top: 161px; width: 241px; height: 582px; text-align: center;
  }
  .label--cream { left: 98px; background: var(--cream); color: var(--maroon-text); }
  .label--maroon { left: 700px; background: var(--maroon); color: var(--cream-text); }

  .label__brand {
    position: absolute; left: 0; right: 0; top: 72px;
    font-family: "Cinzel", serif; font-weight: 400; font-size: 22px; letter-spacing: 0.5px;
  }
  .label__method {
    position: absolute; left: 0; right: 0; top: 244px;
    font-weight: 300; font-size: 14px; line-height: 15px;
  }
  .label__method strong { font-weight: 400; display: block; }
  .label__product {
    position: absolute; left: 0; right: 0; top: 276px;
    font-weight: 300; font-size: 32px; letter-spacing: 0.5px;
  }
  .label__olives { position: absolute; left: 50%; transform: translateX(-50%); border-radius: 46% 46% 40% 40%; }
  .label--cream .label__olives { top: 404px; width: 96px; height: 110px; background: linear-gradient(180deg, #6a4a4c 0%, var(--maroon) 60%); }
  .label--maroon .label__olives { top: 440px; width: 60px; height: 68px; background: linear-gradient(180deg, #d9cfc6 0%, var(--cream-text) 60%); }
  .label__origin {
    position: absolute; left: 0; right: 0; top: 527px; font-weight: 300; font-size: 16px; letter-spacing: 0.3px;
  }
  .label__volume {
    position: absolute; left: 0; right: 0; top: 560px; font-weight: 300; font-size: 11px;
  }

  .label-tag {
    position: absolute; top: 778px; transform: translateX(-50%);
    background: var(--maroon); color: #fff; font-size: 9px; padding: 2px 6px; border-radius: 3px;
  }
</style>
</head>
<body>
<div class="sheet">
  <header class="sheet-header">
    <span>Brindlewood&nbsp;&nbsp;|&nbsp;&nbsp;Extra Virgin Oil Label - 145x60 <span style="text-transform:none">mm</span></span>
    <span>27.Feb.2013</span>
  </header>

  <div class="dimension-width" style="left:98px;width:241px"><span>60</span></div>
  <div class="dimension-height" style="left:63px"><span>145</span></div>
  <section class="label label--cream">
    <div class="label__brand">BRINDLEWOOD</div>
    <div class="label__method">cold pressed<strong>extra virgin</strong></div>
    <div class="label__product">Olive Oil</div>
    <div class="label__olives" role="img" aria-label="Illustration of a sprig of three olives with leaves"></div>
    <div class="label__origin">Australian</div>
    <div class="label__volume">1 litre</div>
  </section>
  <div class="label-tag" style="left:222px">Label 9</div>

  <div class="dimension-width" style="left:700px;width:241px"><span>60</span></div>
  <div class="dimension-height" style="left:665px"><span>145</span></div>
  <section class="label label--maroon">
    <div class="label__brand">BRINDLEWOOD</div>
    <div class="label__method">cold pressed<strong>extra virgin</strong></div>
    <div class="label__product">Olive Oil</div>
    <div class="label__olives" role="img" aria-label="Illustration of a sprig of three olives with leaves"></div>
    <div class="label__origin">Australian</div>
    <div class="label__volume">1 litre</div>
  </section>
  <div class="label-tag" style="left:822px">Label 10</div>

  <div class="sheet-footer-rule"></div>
</div>
</body>
</html>
```